Coastline Premier Retreats Business Card Design

Design a business card for Coastline Premier Retreats. Look at the website for colors and reference. Card should have logo, name, title, office number, mobile number, email, URL and a tagline like, "Luxury Hotel & Resort Email Marketing" (This might change).

https://www.coastlinepremierretreats.example

The rest I will leave up to your imagination.

Contact Information for Business Card

Logo, name, title, office number, mobile number, email, URL and a tagline like, "Luxury Hotel & Resort Email Marketing" (This might change).

```html
<!DOCTYPE html>
<html lang="en">
<head>
<meta charset="UTF-8">
<title>Coastline Premier Retreats – Business Card</title>
<link href="https://fonts.googleapis.com/css2?family=Montserrat:wght@400;500;700;800&display=swap" rel="stylesheet">
<style>
  :root{
    --bg:#d9d9d9;
    --orange:#e26f22;
    --orange-light:#ea8a48;
    --ink:#2e2f30;
    --black:#0b0b0c;
    --charcoal:#3f4142;
    --white:#ffffff;
    --paper:#fcfcfc;
  }
  *{margin:0;padding:0;box-sizing:border-box}
  html,body{width:1200px;height:1200px;overflow:hidden}
  body{
    background:var(--bg);
    font-family:"Montserrat",Arial,sans-serif;
    display:flex;flex-direction:column;align-items:center;justify-content:center;gap:60px;
  }
  .card{
    width:840px;height:480px;border-radius:22px;overflow:hidden;position:relative;
    box-shadow:0 10px 28px rgba(0,0,0,.22);
  }
  /* Front */
  .card-front{background:var(--paper);display:flex;flex-direction:column}
  .front-logo{flex:1;display:flex;align-items:center;justify-content:center}
  .brand-name{
    color:var(--ink);font-weight:800;font-size:46px;letter-spacing:3px;text-transform:uppercase;
    text-align:center;line-height:1.15;
  }
  .front-band{
    height:96px;background:linear-gradient(90deg,var(--charcoal),var(--black) 45%);
    color:var(--white);display:flex;align-items:center;justify-content:center;
    font-size:22px;font-weight:500;letter-spacing:.5px;
  }
  /* Back */
  .card-back{
    background:linear-gradient(120deg,var(--charcoal) 0%,var(--black) 45%,var(--black) 100%);
    color:var(--white);
  }
  .back-brand{
    position:absolute;left:40px;top:34px;right:40px;
    color:var(--orange);font-weight:800;font-size:52px;letter-spacing:2px;text-transform:uppercase;line-height:1.05;
  }
  .person{position:absolute;left:120px;top:262px}
  .person-name{color:var(--orange);font-weight:800;font-size:34px}
  .person-title{font-size:20px;margin-top:6px;margin-left:28px}
  .contact-list{position:absolute;left:430px;top:190px;list-style:none}
  .contact-list li{display:flex;align-items:center;gap:12px;font-size:18px;height:34px}
  .contact-list svg{width:18px;height:18px;fill:var(--orange);flex:none}
  .back-band{
    position:absolute;left:0;right:0;bottom:0;height:78px;
    background:linear-gradient(90deg,var(--orange-light),var(--orange));
    display:flex;align-items:center;justify-content:center;font-size:21px;font-weight:500;letter-spacing:.5px;
  }
</style>
</head>
<body>
  <section class="card card-front">
    <div class="front-logo">
      <div class="brand-name">Coastline<br>Premier Retreats</div>
    </div>
    <div class="front-band">Luxury Hotel &amp; Resort Email Marketing</div>
  </section>

  <section class="card card-back">
    <div class="back-brand">Coastline<br>Premier Retreats</div>
    <div class="person">
      <div class="person-name">Jordan Hale</div>
      <div class="person-title">Founder &amp; Director</div>
    </div>
    <ul class="contact-list">
      <li><svg viewBox="0 0 24 24"><path d="M6.6 10.8a15.1 15.1 0 0 0 6.6 6.6l2.2-2.2a1 1 0 0 1 1-.25 11.4 11.4 0 0 0 3.6.57 1 1 0 0 1 1 1V20a1 1 0 0 1-1 1A17 17 0 0 1 3 4a1 1 0 0 1 1-1h3.5a1 1 0 0 1 1 1c0 1.25.2 2.45.57 3.57a1 1 0 0 1-.25 1z"/></svg>555.214.3800</li>
      <li><svg viewBox="0 0 24 24"><path d="M7 2h10a2 2 0 0 1 2 2v16a2 2 0 0 1-2 2H7a2 2 0 0 1-2-2V4a2 2 0 0 1 2-2zm0 3v13h10V5zm5 14.2a1 1 0 1 0 0 2 1 1 0 0 0 0-2z"/></svg>555-309-7142</li>
      <li><svg viewBox="0 0 24 24"><path d="M2 5h20v14H2zm2 2v.5l8 5 8-5V7zm0 2.8V17h16V9.8l-8 5z"/></svg>info@coastlinepremierretreats.example</li>
      <li><svg viewBox="0 0 24 24"><path d="M12 2a10 10 0 1 0 0 20 10 10 0 0 0 0-20zm6.9 9h-3a15 15 0 0 0-1.3-5.6A8 8 0 0 1 18.9 11zM12 4.1c.9 1.2 1.8 3.4 1.9 6.9h-3.8c.1-3.5 1-5.7 1.9-6.9zM9.4 5.4A15 15 0 0 0 8.1 11h-3a8 8 0 0 1 4.3-5.6zM5.1 13h3a15 15 0 0 0 1.3 5.6A8 8 0 0 1 5.1 13zm6.9 6.9c-.9-1.2-1.8-3.4-1.9-6.9h3.8c-.1 3.5-1 5.7-1.9 6.9zm2.6-1.3a15 15 0 0 0 1.3-5.6h3a8 8 0 0 1-4.3 5.6z"/></svg>www.coastlinepremierretreats.example</li>
    </ul>
    <div class="back-band">North America, 4170 Harbor Lane Seabrook Maine 04000</div>
  </section>
</body>
</html>
```